wardrobe/costume stylist needs good business card for own business

Hi:)

I'm wanting a business card for my company. I am a freelance stylist.

I do wardrobe/costume stylist to TV commercials; Films; Fashion and Lifestyle shoots.

I'd like a design based around my name Rosalind Parfrey written nicely, maybe a colour? Up to you?!

I've attached a couple of images of business cards I like
.... be creative and have fun!

Thank you :)

Reason: I was trying to get my new business card ready for before I headed overseas Friday morning but I don't think that was realistic so I'd like to extend the deadline to give time to the project. Thank you

Hi designers:) Thank you for all your designs, I've extended the deadline until Sunday, so there's a bit more time. I've attached 3 pictures of business cards which I quite like, please take a look to see if it can be of help in your process. I like the pale plain or patterned background with dark font and the dark plain or patterned background with the pale font the motifs the feminine fonts the plain fonts I like the idea of playing with a circle or some shape on one side of the card with my name or initials as in the picture I have on my post could you play around with this idea a bit please? Thank you all for the work you've done :) Rosa

Hi I am working overseas til Saturday night sorry for no feedback until I teturn Thanks :) Rosa

Hi designers, Thank you all so much for submitting your designs, I really appreciate your input into my project :) I'm sorry I didn't get to respond to some comments, and give feedback. I didn't back from being away until later than I expected, and the deadline had passed then, so apologies. Thanks to you all again for all your really good designs :) Rosa

Target Market(s)

I am a freelance stylist my target audience is producers, production companies, photographers, directors...

Industry/Entity Type

Business

Requirements
Must have
• Rosalind Parfrey
Stylist or Wardrobe Stylist

email rosaparfrey@mailbox-example.co.nz
Mobile 0218467193

(Don't have to use the words 'email' and 'mobile')
Nice to have
• Would like it to be double sided
Like B & W
Like pale colour background with dark font or white font
Like dark colour background with pale font
Should not have
• I would prefer it not to incorporate pictures

```html
<!DOCTYPE html>
<html lang="en">
<head>
<meta charset="utf-8">
<title>Rosalind Parfrey – Wardrobe Stylist</title>
<link rel="stylesheet" href="https://fonts.googleapis.com/css2?family=Oswald:wght@300;400;600&family=Pirata+One&display=swap">
<style>
  :root {
    --card-brown: #4b2613;
    --card-brown-light: #55301b;
    --card-brown-dark: #42200f;
    --ink-white: #ffffff;
  }
  html, body {
    margin: 0;
    padding: 0;
    width: 1200px;
    height: 702px;
    overflow: hidden;
    background: var(--card-brown);
  }
  .business-card {
    position: relative;
    width: 1200px;
    height: 702px;
    overflow: hidden;
    background:
      radial-gradient(ellipse at 30% 25%, var(--card-brown-light) 0%, transparent 60%),
      radial-gradient(ellipse at 80% 85%, var(--card-brown-dark) 0%, transparent 55%),
      var(--card-brown);
    color: var(--ink-white);
    font-family: "Oswald", sans-serif;
  }
  .monogram-ring {
    position: absolute;
    left: 116px;
    top: 171px;
    width: 328px;
    height: 328px;
  }
  .monogram-initials {
    position: absolute;
    left: 116px;
    top: 171px;
    width: 328px;
    height: 328px;
    display: flex;
    align-items: center;
    justify-content: center;
    font-family: "Oswald", sans-serif;
    font-weight: 300;
    font-size: 130px;
    letter-spacing: 6px;
    line-height: 1;
  }
  .divider {
    position: absolute;
    left: 487px;
    top: 208px;
    width: 2px;
    height: 292px;
    background: var(--ink-white);
  }
  .stylist-name {
    position: absolute;
    left: 522px;
    top: 200px;
    margin: 0;
    font-family: "Pirata One", serif;
    font-weight: 400;
    font-size: 58px;
    line-height: 1;
    letter-spacing: 1px;
  }
  .stylist-role {
    position: absolute;
    left: 532px;
    top: 286px;
    margin: 0;
    font-family: "Oswald", sans-serif;
    font-weight: 400;
    font-size: 30px;
    line-height: 1;
    letter-spacing: 2.5px;
  }
  .contact-label {
    position: absolute;
    left: 522px;
    margin: 0;
    font-family: "Oswald", sans-serif;
    font-weight: 600;
    font-size: 56px;
    line-height: 1;
  }
  .contact-label--mobile { top: 362px; }
  .contact-label--email { top: 446px; }
  .contact-value {
    position: absolute;
    left: 645px;
    margin: 0;
    font-family: "Oswald", sans-serif;
    font-weight: 300;
    line-height: 1;
    letter-spacing: 1px;
  }
  .contact-value--mobile { top: 366px; font-size: 46px; }
  .contact-value--email { top: 460px; font-size: 37px; letter-spacing: 0.5px; }
</style>
</head>
<body>
  <main class="business-card">
    <svg class="monogram-ring" viewBox="0 0 328 328" aria-hidden="true">
      <circle cx="164" cy="164" r="162" fill="none" stroke="#ffffff" stroke-width="3"/>
    </svg>
    <div class="monogram-initials">RP</div>

    <div class="divider"></div>

    <h1 class="stylist-name">Rosalind Parfrey</h1>
    <p class="stylist-role">WARDROBE STYLIST</p>

    <p class="contact-label contact-label--mobile">M</p>
    <p class="contact-value contact-value--mobile">0218467193</p>

    <p class="contact-label contact-label--email">E</p>
    <p class="contact-value contact-value--email">rosaparfrey@mailbox-example.co.nz</p>
  </main>
</body>
</html>
```